Puffy Clouds Cotton Candy

Looking for a logo design and business cards to help a 13 year old entrepreneur promote her cotton candy business.
Contact Information for Business Card
Name, Phone & Email
Colors
E54698
E96AAD
F1A4CE
F9D9EA
FCEFF6
A7469A
B969AE
D3A5CF
EDDBEB
F8F0F9
6B429C
8869AF
B7A5CE
E3DAEB
F3F0F8
Requirements
Must have
- A fun feel that is appropriate for a teenage girl selling cotton candy

```html
<!DOCTYPE html>
<html lang="en">
<head>
<meta charset="utf-8">
<title>Puffy Clouds Cotton Candy — Business Cards</title>
<link href="https://fonts.googleapis.com/css2?family=Jost:wght@500;600&family=Arimo:wght@400&display=swap" rel="stylesheet">
<style>
  :root {
    --stage: #0d0d0e;
    --card: #262628;
    --card-back: #2a2a2c;
    --pink: #e54698;
    --purple: #6b429c;
    --purple-soft: #8869af;
    --white: #f4f4f4;
    --rule: #6e6e70;
    --emboss: #3b3b3d;
    --emboss-edge: #4a4a4c;
  }
  * { box-sizing: border-box; margin: 0; padding: 0; }
  html, body {
    width: 1200px; height: 820px; overflow: hidden;
    background: var(--stage);
  }
  .stage {
    position: relative; width: 1200px; height: 820px;
    display: flex; align-items: center; justify-content: center; gap: 40px;
  }
  .card {
    position: relative; width: 560px; height: 320px;
    background: var(--card);
    border-bottom: 3px solid var(--pink);
    border-left: 3px solid var(--pink);
    box-shadow: 0 18px 40px rgba(0,0,0,.6);
    overflow: hidden;
  }
  .card--back { background: var(--card-back); }

  .brand {
    position: absolute; display: flex; align-items: center; gap: 14px;
    font-family: "Jost", sans-serif; font-weight: 600; color: var(--pink);
  }
  .brand__dot {
    border-radius: 50%; border: 4px solid var(--pink); flex: none;
  }
  .brand__name { line-height: 1.02; }

  .card--front .brand { left: 200px; top: 38px; }
  .card--front .brand__dot { width: 76px; height: 76px; }
  .card--front .brand__name { font-size: 26px; }

  .person {
    position: absolute; left: 48px; top: 150px;
    font-family: "Jost", sans-serif;
  }
  .person__name { font-size: 23px; font-weight: 600; color: var(--pink); line-height: 1.05; }
  .person__role { font-size: 15px; font-weight: 500; color: var(--purple-soft); margin-top: 1px; }

  .rule {
    position: absolute; left: 48px; right: 40px; top: 204px;
    height: 1px; background: var(--rule);
  }

  .contact {
    position: absolute; left: 48px; top: 220px;
    font-family: "Arimo", sans-serif; font-size: 15px; color: var(--white);
    list-style: none;
  }
  .contact li { display: flex; align-items: center; gap: 8px; line-height: 24px; }
  .contact svg { width: 15px; height: 15px; flex: none; }

  .address {
    position: absolute; right: 40px; top: 222px; text-align: right;
    font-family: "Arimo", sans-serif; font-size: 14px; color: var(--white); line-height: 1.35;
  }

  .seal {
    position: absolute; left: 40px; top: 26px; width: 268px; height: 268px;
    border-radius: 50%;
    background: var(--emboss);
    border: 3px solid var(--emboss-edge);
    box-shadow: inset 0 2px 6px rgba(0,0,0,.5), 0 1px 0 rgba(255,255,255,.06);
  }
  .card--back .brand { right: 34px; top: 118px; text-align: left; }
  .card--back .brand__name { font-size: 30px; }
</style>
</head>
<body>
<main class="stage">
  <section class="card card--front" aria-label="Business card front">
    <div class="brand">
      <span class="brand__dot"></span>
      <span class="brand__name">Puffy Clouds<br>Cotton Candy</span>
    </div>
    <div class="person">
      <p class="person__name">Maya Bennett</p>
      <p class="person__role">Managing Director</p>
    </div>
    <div class="rule"></div>
    <ul class="contact">
      <li>
        <svg viewBox="0 0 24 24" aria-hidden="true"><path fill="#e54698" d="M6.6 10.8a15.1 15.1 0 0 0 6.6 6.6l2.2-2.2a1 1 0 0 1 1-.25 11.4 11.4 0 0 0 3.6.57 1 1 0 0 1 1 1V20a1 1 0 0 1-1 1A17 17 0 0 1 3 4a1 1 0 0 1 1-1h3.5a1 1 0 0 1 1 1c0 1.25.2 2.45.57 3.57a1 1 0 0 1-.25 1z"/></svg>
        055-210 348 671
      </li>
      <li>
        <svg viewBox="0 0 24 24" aria-hidden="true"><path fill="#e54698" d="M2 5h20v14H2z"/><path fill="none" stroke="#262628" stroke-width="2" d="M2 5l10 8 10-8"/></svg>
        hello@puffyclouds.com
      </li>
    </ul>
    <div class="address">88, Maple Lane, Suite 4<br>30417,Sample Country</div>
  </section>

  <section class="card card--back" aria-label="Business card back">
    <div class="seal"></div>
    <div class="brand">
      <span class="brand__name">Puffy Clouds<br>Cotton Candy</span>
    </div>
  </section>
</main>
</body>
</html>
```